KRL Stationery Design Project

Dear Designers,
We need a new stationery design for company to match our new logo.
Designers should provide a design for the following:
1. Business Card: 3.5x2 Inches.
2. Letterhead: A4 size.
3. Envelops: 25x35.5 Cm.
You can keep the Arabic name at the bottom of the logo Or you can use the separate attached Arabic Name.
Please refer to the attached logo guide for design information.
Sample Business Card information:
Name: Tarek Sowan
Position: Operation Manager
Tel: +966 920007164 Ex. 500
Fax: +966 (3)8842617
Mob: +966 (5)00263817
email: tarek@krl-example.com.sa
URL: www.krl-example.com.sa
Address:
Nakheel Heights, Suite 718
Zayed bin Omar Str.
Khobar, 31847
Saudi Arabia
Updates
Dear All,
Please note, we had uploaded our logo along with Arabic writing in Adobe illustrator format (.ai).
Regards,
Karim
Dear All,
A sample data for the business card had been added as per your request.
Regards,
Karim

```html
<!DOCTYPE html>
<html lang="en">
<head>
<meta charset="utf-8">
<title>KRL Business Card</title>
<link rel="stylesheet" href="https://fonts.googleapis.com/css2?family=Open+Sans:wght@400;700&display=swap">
<style>
  :root {
    --stage: #1e1e1e;
    --card: #ffffff;
    --navy: #1f3a5c;
    --ink: #3f4448;
    --muted: #5a5f63;
    --rule: #c9cbcd;
  }
  * { margin: 0; padding: 0; box-sizing: border-box; }
  html, body {
    width: 1200px;
    height: 472px;
    overflow: hidden;
    background: var(--stage);
    font-family: "Open Sans", Arial, sans-serif;
  }
  .canvas { position: relative; width: 1200px; height: 472px; }
  .card {
    position: absolute;
    background: var(--card);
    border-radius: 14px;
    width: 524px;
    height: 300px;
    top: 84px;
  }
  .card--front { left: 60px; }
  .card--back { left: 603px; }

  .brand {
    position: absolute;
    display: flex;
    align-items: center;
    gap: 12px;
    color: var(--navy);
    font-weight: 700;
  }
  .brand__mark { background: var(--navy); display: block; }
  .card--front .brand { left: 70px; top: 108px; font-size: 52px; line-height: 1; }
  .card--front .brand__mark { width: 26px; height: 26px; }
  .card--back .brand { left: 0; right: 0; top: 85px; justify-content: center; font-size: 72px; line-height: 1; }
  .card--back .brand__mark { width: 34px; height: 34px; }

  .divider {
    position: absolute;
    left: 306px;
    top: 86px;
    width: 1px;
    height: 163px;
    background: var(--rule);
  }
  .details { position: absolute; left: 324px; top: 80px; }
  .person { color: var(--navy); font-size: 17px; font-weight: 700; line-height: 22px; }
  .person__title { font-weight: 400; font-size: 14px; }
  .contacts { list-style: none; margin-top: 19px; }
  .contacts li {
    display: flex;
    align-items: center;
    gap: 6px;
    font-size: 14px;
    line-height: 17px;
    color: var(--ink);
  }
  .contacts svg { width: 11px; height: 11px; fill: var(--ink); flex: none; }
  .address { margin-top: 15px; font-size: 14px; line-height: 18px; color: var(--muted); font-style: normal; }

  .web {
    position: absolute;
    left: 0; right: 0;
    top: 244px;
    text-align: center;
    font-size: 13px;
    letter-spacing: 2.6px;
    color: var(--muted);
  }
</style>
</head>
<body>
<main class="canvas">
  <section class="card card--front">
    <div class="brand"><span class="brand__mark"></span>KRL</div>
    <span class="divider"></span>
    <div class="details">
      <p class="person">Your Name, <span class="person__title">Title</span></p>
      <ul class="contacts">
        <li><svg viewBox="0 0 12 12"><path d="M2.5 0.5 4.5 3 3.4 4.3c.7 1.7 2.1 3.1 3.9 3.9L8.6 7l2.6 2-1 2.4C5.4 11.2.9 6.7.4 1.6z"/></svg>123-456-7890</li>
        <li><svg viewBox="0 0 12 12"><rect x="3" y="0.5" width="6" height="11" rx="1.2"/><rect x="4" y="2" width="4" height="6.5" fill="#fff"/></svg>123-456-7890</li>
        <li><svg viewBox="0 0 12 12"><rect x="0.5" y="2" width="11" height="8" rx="1"/><path d="M1 2.8 6 6.5l5-3.7" stroke="#fff" stroke-width="1.1" fill="none"/></svg>info@krl-example.com.sa</li>
        <li><svg viewBox="0 0 12 12"><circle cx="6" cy="6" r="5.5"/><path d="M.5 6h11M6 .5c-2.4 3-2.4 8 0 11M6 .5c2.4 3 2.4 8 0 11" stroke="#fff" stroke-width=".9" fill="none"/></svg>www.website.com</li>
      </ul>
      <address class="address">Street Name, City Name<br>State, City Zip Code</address>
    </div>
  </section>

  <section class="card card--back">
    <div class="brand"><span class="brand__mark"></span>KRL</div>
    <p class="web">www.website.com</p>
  </section>
</main>
</body>
</html>
```